New Business Card Design Project

Use the flyer uploaded and website www.brightoakbuilders.com for inspiration.
List Our Services on Backside of business cards
Marcus Delling
Harborline Builders Inc.
Licensed General Contractors
858-471-6093

Contact Information for Business Card

Use the flyer uploaded and website www.brightoakbuilders.com for inspiration. List Our Services on Backside of business cards Marcus Delling Harborline Builders Inc. Licensed General Contractors 858-471-6093

```html
<!DOCTYPE html>
<html lang="en">
<head>
<meta charset="utf-8">
<title>Harborline Builders Inc. – Business Cards</title>
<link href="https://fonts.googleapis.com/css2?family=Montserrat:wght@400;500;700&display=swap" rel="stylesheet">
<style>
  :root{
    --stage:#2b2522;
    --card:#141414;
    --ink:#f2f2f2;
    --ink-soft:#cfcfcf;
    --rule:#e6e6e6;
  }
  *{box-sizing:border-box;margin:0;padding:0}
  html,body{width:1200px;height:716px;overflow:hidden}
  body{
    background:var(--stage);
    font-family:"Montserrat",Arial,sans-serif;
    color:var(--ink);
    display:flex;align-items:center;justify-content:center;gap:40px;
  }
  .card{
    position:relative;
    width:540px;height:309px;
    background:var(--card);
    border-radius:4px;
    overflow:hidden;
    box-shadow:0 10px 30px rgba(0,0,0,.45);
  }
  .wordmark{
    display:flex;align-items:center;gap:10px;
    font-weight:400;
    letter-spacing:.16em;
    text-transform:uppercase;
    color:var(--ink);
  }
  .wordmark-dot{width:10px;height:10px;border-radius:50%;background:var(--ink)}
  .wordmark-name{font-size:20px}

  /* Back: services */
  .card-back .wordmark{position:absolute;top:42px;left:0;right:0;justify-content:center}
  .services-heading{
    position:absolute;top:102px;left:36px;right:36px;
    display:flex;align-items:center;gap:14px;
    font-weight:700;font-size:14px;letter-spacing:.04em;
  }
  .services-heading::before,.services-heading::after{
    content:"";flex:1;height:1.5px;background:var(--rule);
  }
  .services-list{
    position:absolute;top:138px;left:40px;right:30px;
    display:grid;grid-template-columns:1fr 1fr;column-gap:24px;
  }
  .services-list ul{list-style:none}
  .services-list li{
    display:flex;align-items:center;gap:8px;
    font-size:13px;line-height:23px;color:var(--ink);
  }
  .tick{width:12px;height:12px;flex:none}

  /* Front: contact */
  .card-front .wordmark{position:absolute;top:54px;left:0;right:0;justify-content:center}
  .person{position:absolute;top:118px;left:44px}
  .person-name{font-weight:700;font-size:26px;line-height:1.1}
  .person-role{font-weight:700;font-size:14px;margin-top:4px}
  .person-rule{width:150px;height:1.5px;background:var(--rule);margin-top:10px}
  .contact{position:absolute;top:200px;left:44px;list-style:none}
  .contact li{display:flex;align-items:center;gap:10px;font-size:14px;line-height:28px;color:var(--ink-soft)}
  .contact svg{width:15px;height:15px;flex:none}
</style>
</head>
<body>

<section class="card card-back" aria-label="Business card back – services">
  <div class="wordmark"><span class="wordmark-dot"></span><span class="wordmark-name">Harborline Builders</span></div>
  <h2 class="services-heading">OUR SERVICES</h2>
  <div class="services-list">
    <ul>
      <li><svg class="tick" viewBox="0 0 12 12"><rect x=".75" y=".75" width="10.5" height="10.5" fill="none" stroke="#f2f2f2" stroke-width="1.3"/><path d="M3 6.2l2 2 4-4.5" fill="none" stroke="#f2f2f2" stroke-width="1.5"/></svg>Remodel: Kitchen &amp; Bath</li>
      <li><svg class="tick" viewBox="0 0 12 12"><rect x=".75" y=".75" width="10.5" height="10.5" fill="none" stroke="#f2f2f2" stroke-width="1.3"/><path d="M3 6.2l2 2 4-4.5" fill="none" stroke="#f2f2f2" stroke-width="1.5"/></svg>Painting: Interior &amp; Exterior</li>
      <li><svg class="tick" viewBox="0 0 12 12"><rect x=".75" y=".75" width="10.5" height="10.5" fill="none" stroke="#f2f2f2" stroke-width="1.3"/><path d="M3 6.2l2 2 4-4.5" fill="none" stroke="#f2f2f2" stroke-width="1.5"/></svg>Flooring: Carpet, Vinyl, Wood</li>
      <li><svg class="tick" viewBox="0 0 12 12"><rect x=".75" y=".75" width="10.5" height="10.5" fill="none" stroke="#f2f2f2" stroke-width="1.3"/><path d="M3 6.2l2 2 4-4.5" fill="none" stroke="#f2f2f2" stroke-width="1.5"/></svg>Window &amp; Door Replacement</li>
    </ul>
    <ul>
      <li><svg class="tick" viewBox="0 0 12 12"><rect x=".75" y=".75" width="10.5" height="10.5" fill="none" stroke="#f2f2f2" stroke-width="1.3"/><path d="M3 6.2l2 2 4-4.5" fill="none" stroke="#f2f2f2" stroke-width="1.5"/></svg>Plumbing: Repairs &amp; Upgrades</li>
      <li><svg class="tick" viewBox="0 0 12 12"><rect x=".75" y=".75" width="10.5" height="10.5" fill="none" stroke="#f2f2f2" stroke-width="1.3"/><path d="M3 6.2l2 2 4-4.5" fill="none" stroke="#f2f2f2" stroke-width="1.5"/></svg>Energy-Efficient Upgrades</li>
      <li><svg class="tick" viewBox="0 0 12 12"><rect x=".75" y=".75" width="10.5" height="10.5" fill="none" stroke="#f2f2f2" stroke-width="1.3"/><path d="M3 6.2l2 2 4-4.5" fill="none" stroke="#f2f2f2" stroke-width="1.5"/></svg>Deck &amp; Patio Construction</li>
    </ul>
  </div>
</section>

<section class="card card-front" aria-label="Business card front – contact">
  <div class="wordmark"><span class="wordmark-dot"></span><span class="wordmark-name">Harborline Builders</span></div>
  <div class="person">
    <h1 class="person-name">Marcus Delling</h1>
    <p class="person-role">Licensed General Contractors</p>
    <div class="person-rule"></div>
  </div>
  <ul class="contact">
    <li><svg viewBox="0 0 16 16" aria-hidden="true"><path d="M4 1.5l2.3 3-1.4 1.6c.8 1.9 2.2 3.4 4.2 4.4l1.6-1.4 3 2.3-1.4 2.6C7.5 13.7 2.5 8.7 1.5 3z" fill="none" stroke="#cfcfcf" stroke-width="1.3" stroke-linejoin="round"/></svg>858-471-6093</li>
    <li><svg viewBox="0 0 16 16" aria-hidden="true"><g fill="none" stroke="#cfcfcf" stroke-width="1.2"><circle cx="8" cy="8" r="6.5"/><ellipse cx="8" cy="8" rx="3" ry="6.5"/><path d="M1.5 8h13M2.5 4.8h11M2.5 11.2h11"/></g></svg>www.brightoakbuilders.com</li>
  </ul>
</section>

</body>
</html>
```